New business card/stationary for a consulting company

I am looking for a clean and very professional looking business card for my consulting company as well as corresponding stationary. I am uploading our logo. I like simple and powerful for the feel. No graphics but I am open on everything else. Below is my contact information but would like the final to be in a version I can add my employees information into and print. Thank you.

Daniel Whitcombe
dan@ferncliffadvisory.com
2870 North 9th Avenue, Summit Floor, Elm Ridge, Illinois 60531
www.ferncliffadvisory.com

Industry/Entity Type

Consulting

Contact Information for Business Card

Daniel Whitcombe
dan@ferncliffadvisory.com
www.ferncliffadvisory.com

Font styles to use
Serif
Sans Serif

Requirements
Must have
• Our logo and the business card details.
Nice to have
• our website www.ferncliffadvisory.com

```html
<!DOCTYPE html>
<html lang="en">
<head>
<meta charset="utf-8">
<title>Ferncliff Advisory — Business Card</title>
<link rel="stylesheet" href="https://fonts.googleapis.com/css2?family=Open+Sans:wght@300;400;600;700&family=PT+Sans+Narrow:wght@700&display=swap">
<style>
  :root {
    --page: #e6e7eb;
    --navy: #1f1f7a;
    --blue-bright: #1d1dd6;
    --blue-deep: #08085c;
    --paper: #fbfbfb;
    --ink: #4a4a4a;
    --rule: #2a2a8a;
    --white: #ffffff;
  }
  * { box-sizing: border-box; margin: 0; padding: 0; }
  html, body { width: 1200px; height: 900px; overflow: hidden; }
  body {
    background: var(--page);
    font-family: "Open Sans", Arial, sans-serif;
    display: flex;
    flex-direction: column;
    align-items: center;
    justify-content: center;
    gap: 60px;
  }
  .card {
    position: relative;
    width: 560px;
    height: 320px;
    box-shadow: 0 6px 18px rgba(0,0,0,0.18);
    overflow: hidden;
  }

  /* Front side */
  .card-front {
    background: linear-gradient(100deg, var(--blue-bright) 0%, #1414a8 40%, var(--blue-deep) 100%);
    display: flex;
    flex-direction: column;
    align-items: center;
    justify-content: center;
    gap: 54px;
  }
  .front-brand {
    color: var(--white);
    font-family: "Open Sans", Arial, sans-serif;
    font-weight: 400;
    font-size: 34px;
    letter-spacing: 3px;
    text-transform: uppercase;
    margin-top: 20px;
  }
  .front-web {
    color: var(--white);
    font-size: 13px;
    letter-spacing: 5px;
  }

  /* Back side */
  .card-back { background: var(--paper); }
  .back-brand {
    position: absolute;
    top: 52px;
    right: 42px;
    display: flex;
    align-items: center;
    gap: 10px;
  }
  .brand-square {
    width: 16px;
    height: 16px;
    background: var(--navy);
  }
  .brand-name {
    color: var(--navy);
    font-weight: 300;
    font-size: 24px;
    letter-spacing: 1px;
    text-transform: uppercase;
  }
  .rule {
    position: absolute;
    height: 1px;
    background: var(--rule);
  }
  .rule-top { top: 118px; left: 170px; right: 40px; }
  .rule-name { top: 236px; left: 40px; right: 40px; }
  .contact {
    position: absolute;
    top: 132px;
    right: 40px;
    list-style: none;
    text-align: right;
    color: var(--ink);
    font-size: 12.5px;
    line-height: 20px;
  }
  .contact li { display: flex; align-items: center; justify-content: flex-end; gap: 6px; }
  .contact svg { width: 11px; height: 11px; fill: var(--navy); }
  .person-name {
    position: absolute;
    top: 208px;
    left: 40px;
    font-family: "PT Sans Narrow", "Arial Narrow", sans-serif;
    font-weight: 700;
    font-size: 21px;
    color: var(--navy);
    text-transform: uppercase;
    letter-spacing: 0.3px;
  }
  .name-tab {
    position: absolute;
    top: 244px;
    left: 0;
    width: 16px;
    height: 26px;
    background: var(--navy);
  }
  .address {
    position: absolute;
    top: 246px;
    left: 40px;
    font-style: normal;
    color: var(--ink);
    font-size: 13px;
    line-height: 19px;
  }
</style>
</head>
<body>
  <section class="card card-front" aria-label="Business card front">
    <div class="front-brand">Ferncliff Advisory</div>
    <div class="front-web">www.ferncliffadvisory.com</div>
  </section>

  <section class="card card-back" aria-label="Business card back">
    <div class="back-brand">
      <span class="brand-square"></span>
      <span class="brand-name">Ferncliff Advisory</span>
    </div>
    <div class="rule rule-top"></div>
    <ul class="contact">
      <li>dan@ferncliffadvisory.com
        <svg viewBox="0 0 12 12" aria-hidden="true"><rect x="0" y="2" width="12" height="8" rx="1"/><path d="M0.5 2.5 L6 6.5 L11.5 2.5" stroke="#fbfbfb" stroke-width="1" fill="none"/></svg>
      </li>
      <li>www.ferncliffadvisory.com
        <svg viewBox="0 0 12 12" aria-hidden="true"><circle cx="6" cy="6" r="5.5"/><path d="M0.5 6 H11.5 M6 0.5 C3 3 3 9 6 11.5 M6 0.5 C9 3 9 9 6 11.5" stroke="#fbfbfb" stroke-width="0.9" fill="none"/></svg>
      </li>
    </ul>
    <div class="person-name">Daniel Whitcombe</div>
    <div class="rule rule-name"></div>
    <div class="name-tab"></div>
    <address class="address">
      2870 North 9th Avenue<br>
      Summit Floor, Elm Ridge<br>
      Illinois 60531
    </address>
  </section>
</body>
</html>
```